Payment company requires web design

We need a web design for a new company based in Singapore.

The company focuses on providing 2 key products: 1) an alternative payment option (i.e. like quib or trelloquin options) on the traditional checkout process 2) a replacement/outsource of a merchants payment page. Key in the UX flow is a end customer dashboard that manages all payments.

We look to provide a simple, fluid and easy to use payment process. The dashboard is minimalistic that allows easy navigation, review of transactions and all available options through gamification.

The final design should communicate ease of use, flexibility and transparency.

Target Market(s)

The value is for the merchant - retail/travel/insurance companies. However its the merchant's end customers that are the target and who the UX is built for.

Industry/Entity Type

It Company

Logo Text

zelnar

Number of Pages Required

5+ page

Colors
ec1f27

Requirements
Must have
• 7 pages mimicking UX flow
• payment page * 2 - 1) alternative payment type 2) outsource of merchants payment page to our business
• our landing page
• end customer verification page
• end customer registration
• customer dashboard
• UX flow in attached file
Nice to have
• open to ideas
• have asked for the logo to be added
• logo to have the colour red (chinese for prosperity)
• the company is all about flexibility, transparency in personal finance management with the option of instalment payments

```html
<!DOCTYPE html>
<html lang="en">
<head>
<meta charset="utf-8">
<title>Zelnar — Payment processing</title>
<link href="https://fonts.googleapis.com/css2?family=Raleway:wght@300;400;500;600;700&family=Open+Sans:wght@400;600;700&display=swap" rel="stylesheet">
<style>
:root{
  --red:#ec1f27;
  --dark:#2b2b2b;
  --text:#555;
  --muted:#7a7a7a;
  --light:#f2f2f2;
  --white:#fff;
  --hero-a:#1d2740;
  --hero-b:#3b4a70;
  --about-a:#3a4654;
  --about-b:#5d6f82;
}
*{box-sizing:border-box;margin:0;padding:0}
html,body{width:1200px;height:3077px;overflow:hidden;background:var(--white)}
body{font-family:"Open Sans",Arial,sans-serif;color:var(--text);position:relative}
.abs{position:absolute}

/* hero */
.hero{left:0;top:0;width:1200px;height:702px;background:linear-gradient(180deg,var(--hero-a) 0%,var(--hero-b) 55%,#24304d 100%)}
.brand{left:72px;top:38px;display:flex;align-items:center;gap:10px;font-family:"Raleway",sans-serif;font-size:32px;font-weight:500;color:var(--white);letter-spacing:1px}
.brand-mark{width:14px;height:14px;background:var(--red)}
.nav{top:50px;font-family:"Raleway",sans-serif;font-size:13px;font-weight:500;color:var(--white);text-transform:uppercase}
.btn{background:var(--red);color:var(--white);font-family:"Raleway",sans-serif;font-weight:700;text-transform:uppercase;display:flex;align-items:center;justify-content:center;gap:8px;border-radius:2px}
.reg{left:968px;top:37px;width:154px;height:39px;font-size:13px}
.hero-title{left:0;width:1200px;top:296px;text-align:center;font-family:"Raleway",sans-serif;font-size:56px;font-weight:400;color:var(--white);letter-spacing:2px}
.hero-sub{left:0;width:1200px;top:368px;text-align:center;font-family:"Raleway",sans-serif;font-size:27px;color:var(--white)}
.hero-sub b{font-weight:700}
.contact-btn{left:521px;top:429px;width:158px;height:45px;font-size:13px}
.down{left:582px;top:618px}

/* sections */
.title{left:0;width:1200px;text-align:center;font-family:"Raleway",sans-serif;font-size:38px;color:var(--dark);font-weight:400}
.title b{font-weight:700}
.lead{left:0;width:1200px;text-align:center;font-size:15px;color:var(--text)}

.card{top:937px;width:333px;height:337px}
.card.active{background:var(--red);color:var(--white)}
.card svg{position:absolute;left:52px;top:62px}
.card h3{position:absolute;top:163px;left:52px;font-family:"Raleway",sans-serif;font-size:23px;font-weight:700;color:var(--dark)}
.card.active h3{color:var(--white)}
.card p{position:absolute;top:205px;left:52px;width:240px;font-size:13px;line-height:27px;color:var(--muted)}
.card.active p{color:var(--white)}

.about{left:0;top:1374px;width:1200px;height:507px;background:linear-gradient(120deg,var(--about-a),var(--about-b) 60%,#44536a)}
.about-title{color:var(--white);top:1500px}
.about-text{left:170px;width:860px;top:1574px;text-align:center;font-size:13.5px;line-height:35px;color:var(--white)}
.more-btn{left:523px;top:1708px;width:152px;height:42px;font-size:13px}

.faq-icon{width:58px;height:58px;border-radius:50%;background:var(--red);display:flex;align-items:center;justify-content:center}
.faq-q{font-family:"Raleway",sans-serif;font-weight:700;font-size:16px;line-height:27px;color:var(--dark);width:400px}
.faq-a{font-size:13px;line-height:27px;color:var(--muted);width:400px}
.dot{width:6px;height:6px;border-radius:50%;background:#ccc;top:2330px}

.quote{width:270px;font-size:13px;line-height:24px;color:var(--muted)}
.qmark{font-family:Georgia,serif;font-size:44px;color:#ccc;line-height:1}
.avatar{width:54px;height:54px;border-radius:50%;background:linear-gradient(180deg,#d9d9d9,#a9a9a9);border:3px solid #eee}
.cname{font-family:"Raleway",sans-serif;font-weight:700;font-size:13px;color:var(--red);text-transform:uppercase}
.crole{font-size:12px;color:var(--muted)}

.footer{left:0;top:2761px;width:1200px;height:234px;background:var(--light)}
.fh{top:2800px;font-family:"Raleway",sans-serif;font-weight:700;font-size:16px;color:var(--dark)}
.fl{font-size:12px;color:var(--text);line-height:26px}
.social{width:28px;height:28px;border-radius:50%;background:var(--red);top:2868px}
.copy{left:0;width:1200px;top:3017px;text-align:center;font-size:12px;color:var(--text)}
</style>
</head>
<body>

<section class="abs hero" role="img" aria-label="Night skyline of a waterfront city with lit towers"></section>
<div class="abs brand"><span class="brand-mark"></span>ZELNAR</div>
<nav>
  <span class="abs nav" style="left:420px">Home</span>
  <span class="abs nav" style="left:509px">About us</span>
  <span class="abs nav" style="left:638px">Services</span>
  <span class="abs nav" style="left:765px">FAQ</span>
  <span class="abs nav" style="left:858px">Contact us</span>
</nav>
<div class="abs btn reg">
  <svg width="16" height="16" viewBox="0 0 16 16" fill="none" stroke="#fff" stroke-width="1.6"><rect x="1.5" y="3" width="11" height="11" rx="1"/><path d="M7 9l7-7"/></svg>
  Registration
</div>
<h1 class="abs hero-title">ZELNAR</h1>
<p class="abs hero-sub">We are payment processing company from <b>Singapore</b>.</p>
<div class="abs btn contact-btn">
  <svg width="13" height="13" viewBox="0 0 16 16"><path fill="#fff" d="M3 1l3 3-2 2c1 2 3 4 5 5l2-2 3 3-2 3C7 15 1 9 1 3z"/></svg>
  Contact here
</div>
<svg class="abs down" width="36" height="36" viewBox="0 0 36 36" fill="none" stroke="#fff" stroke-width="1.6"><circle cx="18" cy="18" r="17"/><path d="M12 15l6 6 6-6"/></svg>

<h2 class="abs title" style="top:782px"><b>What</b> we do</h2>
<p class="abs lead" style="top:848px">Lorem Ipsum is simply dummy text of the printing and typesetting industry has been the industry's...</p>

<div class="abs card active" style="left:100px">
  <svg width="84" height="84" viewBox="0 0 84 84" fill="none" stroke="#fff" stroke-width="2.4"><path d="M42 6l6 8 10-2 2 10 9 5-4 9 4 9-9 5-2 10-10-2-6 8-6-8-10 2-2-10-9-5 4-9-4-9 9-5 2-10 10 2z"/><circle cx="42" cy="36" r="8"/><path d="M30 56c2-8 7-11 12-11s10 3 12 11"/></svg>
  <h3>Account monitoring</h3>
  <p>Lorem Ipsum is simply dummy text of the printing and typesetting industry, has been the industry...</p>
</div>
<div class="abs card" style="left:433px">
  <svg width="84" height="84" viewBox="0 0 84 84" fill="none" stroke="#555" stroke-width="2.4"><path d="M14 44c0-13 12-21 27-21 5 0 9 1 13 2l9-6v11c4 3 6 7 7 11h5v12h-6c-2 4-5 7-9 9v8h-9v-5c-4 1-9 1-13 0v5h-9v-9c-9-4-15-10-15-17z"/><circle cx="57" cy="38" r="1.5" fill="#555"/><circle cx="44" cy="12" r="6"/></svg>
  <h3>Instant deposit</h3>
  <p>Lorem Ipsum is simply dummy text of the printing and typesetting industry, has been the industry...</p>
</div>
<div class="abs card" style="left:766px">
  <svg width="84" height="84" viewBox="0 0 84 84" fill="none" stroke="#555" stroke-width="2.4"><circle cx="42" cy="46" r="28"/><path d="M36 12h12M42 12v6M16 22l6-6M68 22l-6-6"/><path d="M50 36c-2-3-5-4-8-4-5 0-8 3-8 6 0 8 16 4 16 12 0 4-4 6-8 6-3 0-6-1-8-4M42 28v4M42 56v4"/></svg>
  <h3>Deposits on demand</h3>
  <p>Lorem Ipsum is simply dummy text of the printing and typesetting industry, has been the industry...</p>
</div>

<section class="abs about" role="img" aria-label="Hands typing on a laptop at a desk"></section>
<h2 class="abs title about-title">About <b>Zelnar</b></h2>
<p class="abs about-text">Lorem Ipsum is simply dummy text of the printing and typesetting industry. Lorem Ipsum has been the industry's standard dummy text ever since the 1500s, when an unknown printer took a galley of type and scrambled it to make a type specimen book. It has survived not only five centuries...</p>
<div class="abs btn more-btn">Read more info</div>

<h2 class="abs title" style="top:1978px">Frequently asked <b>Questions?</b></h2>
<p class="abs lead" style="top:2038px;font-size:18px">Lorem Ipsum is simply dummy text of the printing and typesetting industry.</p>

<div class="abs faq-icon" style="left:111px;top:2125px">
  <svg width="26" height="26" viewBox="0 0 26 26" fill="none" stroke="#fff" stroke-width="2"><circle cx="9" cy="15" r="4"/><circle cx="19" cy="8" r="3"/><path d="M9 8v2M9 20v2M3 15h2M13 15h2M19 3v1M19 12v1M14 8h1M23 8h1"/></svg>
</div>
<p class="abs faq-q" style="left:189px;top:2128px">Lorem Ipsum is simply dummy text of the printing and typesetting industry?</p>
<p class="abs faq-a" style="left:189px;top:2193px">Lorem Ipsum is simply dummy text of the printing and typesetting industry. Lorem Ipsum has been the industry's standard dummy text ever since the 1500s...</p>

<div class="abs faq-icon" style="left:625px;top:2125px">
  <svg width="26" height="26" viewBox="0 0 26 26" fill="none" stroke="#fff" stroke-width="2"><rect x="4" y="8" width="12" height="14" rx="2"/><path d="M10 8V5a2 2 0 012-2h8a2 2 0 012 2v10a2 2 0 01-2 2h-4"/></svg>
</div>
<p class="abs faq-q" style="left:702px;top:2128px">Lorem Ipsum is simply dummy text of the printing and typesetting industry?</p>
<p class="abs faq-a" style="left:702px;top:2193px">Lorem Ipsum is simply dummy text of the printing and typesetting industry. Lorem Ipsum has been the industry's standard dummy text ever since the 1500s...</p>

<span class="abs dot" style="left:587px;background:var(--red)"></span>
<span class="abs dot" style="left:597px"></span>
<span class="abs dot" style="left:607px"></span>

<h2 class="abs title" style="top:2414px">What our <b>Client's</b> say</h2>

<span class="abs qmark" style="left:104px;top:2496px">“</span>
<p class="abs quote" style="left:137px;top:2505px">Lorem Ipsum is simply dummy text of the printing and typesetting industry. Lorem Ipsum has been the industry's standard dummy text ever since...</p>
<span class="abs qmark" style="left:370px;top:2570px">”</span>
<div class="abs avatar" role="img" aria-label="Client portrait" style="left:102px;top:2629px"></div>
<span class="abs cname" style="left:172px;top:2640px">Marlo Quenby</span>
<span class="abs crole" style="left:172px;top:2661px">Business man</span>

<span class="abs qmark" style="left:455px;top:2496px">“</span>
<p class="abs quote" style="left:482px;top:2505px">Lorem Ipsum is simply dummy text of the printing and typesetting industry. Lorem Ipsum has been the industry's standard dummy text ever since...</p>
<span class="abs qmark" style="left:723px;top:2570px">”</span>
<div class="abs avatar" role="img" aria-label="Client portrait" style="left:452px;top:2629px"></div>
<span class="abs cname" style="left:522px;top:2640px">Marlo Quenby</span>
<span class="abs crole" style="left:522px;top:2661px">Business man</span>

<span class="abs qmark" style="left:815px;top:2496px">“</span>
<p class="abs quote" style="left:843px;top:2505px">Lorem Ipsum is simply dummy text of the printing and typesetting industry. Lorem Ipsum has been the industry's standard dummy text ever since...</p>
<span class="abs qmark" style="left:1082px;top:2570px">”</span>
<div class="abs avatar" role="img" aria-label="Client portrait" style="left:812px;top:2629px"></div>
<span class="abs cname" style="left:882px;top:2640px">Marlo Quenby</span>
<span class="abs crole" style="left:882px;top:2661px">Business man</span>

<footer>
  <div class="abs footer"></div>
  <h4 class="abs fh" style="left:100px">Privacy Policy</h4>
  <p class="abs fl" style="left:100px;top:2832px;width:360px">Lorem Ipsum is simply dummy text of the printing and typesetting industry. Lorem Ipsum has been the industry...</p>
  <div class="abs btn" style="left:100px;top:2898px;width:109px;height:33px;font-size:12px;text-transform:none;font-family:'Open Sans',sans-serif;font-weight:400">Read more</div>

  <h4 class="abs fh" style="left:519px">Welcome</h4>
  <p class="abs fl" style="left:519px;top:2832px">Home<br>About<br>Services<br>Faq<br>Contact Us</p>

  <h4 class="abs fh" style="left:675px">Contact Info</h4>
  <p class="abs fl" style="left:677px;top:2832px">120 Street name, City name,<br>Counrtry name : 985664</p>
  <p class="abs fl" style="left:677px;top:2884px"><span style="color:var(--red)">&#9990;</span>&nbsp; ( 412 ) 730 - 5186</p>
  <p class="abs fl" style="left:677px;top:2910px"><span style="color:var(--red)">&#9993;</span>&nbsp; info@zelnar.com</p>

  <h4 class="abs fh" style="left:907px">Follow us</h4>
  <p class="abs fl" style="left:909px;top:2832px">Connect with our social network</p>
  <span class="abs social" role="img" aria-label="Social network link" style="left:909px"></span>
  <span class="abs social" role="img" aria-label="Social network link" style="left:943px"></span>
  <span class="abs social" role="img" aria-label="Social network link" style="left:977px"></span>
  <span class="abs social" role="img" aria-label="Social network link" style="left:1011px"></span>
  <span class="abs social" role="img" aria-label="Social network link" style="left:1045px"></span>

  <p class="abs copy">Copyright © 2016, Zelnar. All Rights Reserved</p>
</footer>

</body>
</html>
```